Roofing company in Toronto, Canada needs a logo design and business card design

We need a business card and logo created for our company. Our company is "KLV Roofing" which provides roofing services for commercial and residential customers. We serve customers in the Greater Toronto Area (in Canada) thus the name KLV.

We want the logo and business card to be a modern design displaying professionalism and quality in the work. We would prefer rounded corners for the business cards but are open to other ideas. The cards should be pleasant and appealing to customers.

Target Market(s)

Commercial and Residential customers

Industry/Entity Type

Roofing

Contact Information for Business Card

Logo Text

KLV Roofing

Requirements
Nice to have
• Colours that are pleasing to the eye but at the same time should stand out from other business cards. If the design can incorporate the name of KLV Roofing and the actual concept of roofing that would be nice.
Should not have
• Do not want the business cards or logo to be childish looking. Need to look professionally designed.

```html
<!DOCTYPE html>
<html lang="en">
<head>
<meta charset="utf-8">
<title>KLV Roofing – Business Card</title>
<link rel="stylesheet" href="https://fonts.googleapis.com/css2?family=Open+Sans:wght@400;600;700&display=swap">
<style>
  :root {
    --page-bg: #ece8e1;
    --card-light: #1f72bb;
    --card-deep: #2c51a2;
    --brand-green: #52b13a;
    --brand-orange: #e8521e;
    --title-grey: #8f9bb3;
    --text-white: #ffffff;
    --icon-blue: #4f8fd8;
  }
  * { margin: 0; padding: 0; box-sizing: border-box; }
  html, body {
    width: 1192px;
    height: 1200px;
    overflow: hidden;
    background: var(--page-bg);
    font-family: "Open Sans", Arial, sans-serif;
  }
  .canvas { position: relative; width: 1192px; height: 1200px; }
  .card {
    position: absolute;
    left: 176px;
    width: 838px;
    height: 502px;
    border-radius: 32px;
    overflow: hidden;
  }
  .card-front {
    top: 46px;
    background: linear-gradient(160deg, var(--card-light) 0%, var(--card-deep) 100%);
  }
  .card-back {
    top: 612px;
    background: linear-gradient(160deg, var(--card-deep) 0%, var(--card-light) 100%);
  }
  .brand-lockup {
    position: absolute;
    display: flex;
    align-items: center;
    white-space: nowrap;
  }
  .brand-square {
    flex: none;
    background: var(--brand-orange);
  }
  .brand-name {
    color: var(--brand-green);
    font-weight: 600;
    line-height: 1;
  }
  .card-front .brand-lockup { left: 118px; top: 196px; gap: 26px; }
  .card-front .brand-square { width: 80px; height: 80px; }
  .card-front .brand-name { font-size: 88px; }
  .card-back .brand-lockup { left: 548px; top: 106px; gap: 12px; }
  .card-back .brand-square { width: 32px; height: 32px; }
  .card-back .brand-name { font-size: 30px; }
  .holder-name {
    position: absolute;
    left: 172px;
    top: 200px;
    font-size: 37px;
    font-weight: 700;
    line-height: 1.2;
    color: var(--text-white);
  }
  .holder-title {
    position: absolute;
    left: 172px;
    top: 262px;
    font-size: 17px;
    font-weight: 400;
    color: var(--title-grey);
  }
  .contact-list {
    position: absolute;
    left: 170px;
    top: 313px;
    list-style: none;
  }
  .contact-item {
    display: flex;
    align-items: center;
    height: 35.3px;
    font-size: 17.5px;
    color: var(--text-white);
  }
  .contact-icon {
    width: 18px;
    height: 18px;
    margin-right: 14px;
    flex: none;
  }
</style>
</head>
<body>
<main class="canvas">
  <section class="card card-front" aria-label="Card front">
    <div class="brand-lockup">
      <span class="brand-square" aria-hidden="true"></span>
      <span class="brand-name">KLV Roofing</span>
    </div>
  </section>

  <section class="card card-back" aria-label="Card back">
    <div class="brand-lockup">
      <span class="brand-square" aria-hidden="true"></span>
      <span class="brand-name">KLV Roofing</span>
    </div>
    <h1 class="holder-name">Daniel Marsh</h1>
    <p class="holder-title">general director</p>
    <ul class="contact-list">
      <li class="contact-item">
        <svg class="contact-icon" viewBox="0 0 18 18" aria-hidden="true"><rect x="4" y="1" width="10" height="16" rx="2" fill="none" stroke="var(--icon-blue)" stroke-width="1.6"/></svg>
        416 20 71 904
      </li>
      <li class="contact-item">
        <svg class="contact-icon" viewBox="0 0 18 18" aria-hidden="true"><rect x="1" y="4" width="16" height="11" fill="var(--icon-blue)"/><path d="M1 4 L9 10 L17 4" fill="none" stroke="var(--card-deep)" stroke-width="1.4"/></svg>
        dmarsh@klvroofing.com
      </li>
      <li class="contact-item">
        <svg class="contact-icon" viewBox="0 0 18 18" aria-hidden="true"><g fill="none" stroke="var(--icon-blue)" stroke-width="1.4"><circle cx="9" cy="9" r="7.5"/><ellipse cx="9" cy="9" rx="3.2" ry="7.5"/><line x1="1.5" y1="9" x2="16.5" y2="9"/></g></svg>
        www.klvroofing.com
      </li>
      <li class="contact-item">
        <svg class="contact-icon" viewBox="0 0 18 18" aria-hidden="true"><path d="M9 1 C5.5 1 3.5 3.6 3.5 6.5 C3.5 10.5 9 17 9 17 C9 17 14.5 10.5 14.5 6.5 C14.5 3.6 12.5 1 9 1 Z" fill="var(--icon-blue)"/><circle cx="9" cy="6.6" r="2" fill="var(--card-deep)"/></svg>
        2210 Bayview Lane Northvale, Canada
      </li>
    </ul>
  </section>
</main>
</body>
</html>
```